Inspiring Fundraising Foundation Website to Provide Academic Scholarships

Hello, we are launching a foundation to provide academic scholarships to high school students for college. We'd like this to be an informational website with contact information. There will be a total of approximately 5-7 pages in all.
The color scheme will be purple and white, with a girly feel. I 've attached the logo for reference!

Target Market(s)

high school students, college students

Industry/Entity Type

Education

Coding

Coded - Design and coding required

Number of Pages Required

5+ page

Font styles to use
Serif
Sans Serif
Script

Colors
6b449b
886aae
b7a5cd
e4daeb
ffffff
fdf9cf
fbf289

Requirements
Must have
• Purple, girly feel, to reflect the logo's style. Should be light-themed
Should not have
• No dark themes (aka heavy on black or dark colors)

```html
<!DOCTYPE html>
<html lang="en">
<head>
<meta charset="utf-8">
<title>Lila Moreno Foundation</title>
<link rel="stylesheet" href="https://fonts.googleapis.com/css2?family=Raleway:wght@400;600;700;800&family=Open+Sans:wght@400;600;700&display=swap">
<style>
:root{
  --purple-deep:#6b449b;
  --purple-mid:#886aae;
  --purple-soft:#b7a5cd;
  --lilac:#e4daeb;
  --white:#ffffff;
  --cream:#fdf9cf;
  --yellow:#fbf289;
  --ink:#3a3340;
  --muted:#5e566a;
}
*{margin:0;padding:0;box-sizing:border-box}
html,body{width:805px;height:1200px;overflow:hidden;background:var(--white)}
body{position:relative;font-family:"Open Sans",sans-serif;color:var(--ink)}
.abs{position:absolute}

/* hero */
.hero-bg{left:0;top:0;width:805px;height:410px;background:linear-gradient(180deg,#f3eef8 0%,#ebe3f2 70%,#f7f3fa 100%)}
.hero-photo{left:250px;top:45px;width:555px;height:365px;background:linear-gradient(120deg,#ddd0e8 0%,#c9b3d9 40%,#e8d9c8 70%,#d7c6e4 100%);border-radius:0 0 0 40px}
.hero-curve{left:0;top:300px}
.brand{left:94px;top:150px;width:140px;text-align:center;font-family:"Raleway",sans-serif;font-weight:700;color:var(--purple-deep);font-size:30px;line-height:1.05}
.brand-dot{left:150px;top:104px;width:30px;height:30px;border-radius:50%;background:var(--purple-deep)}
.slider-arrows{left:104px;top:316px;display:flex;gap:10px}

/* nav */
.nav{left:64px;top:8px;width:674px;height:37px;background:var(--purple-deep);border-radius:19px;display:flex;align-items:center;overflow:hidden}
.nav a{font-size:10px;color:var(--white);text-decoration:none;padding:0 12px;height:37px;line-height:37px}
.nav a.active{background:var(--yellow);color:var(--purple-deep);margin-left:14px;padding:0 13px}
.nav-phone{position:absolute;right:0;top:0;width:128px;height:37px;background:var(--purple-mid);display:flex;align-items:center;justify-content:center;gap:10px;color:var(--white);font-size:13px}

/* banner */
.banner{left:64px;top:342px;width:674px;height:99px;border-radius:16px;background:linear-gradient(180deg,var(--purple-mid),var(--purple-deep));box-shadow:0 4px 10px rgba(107,68,155,.25)}
.banner-text{left:59px;top:28px;font-family:"Raleway",sans-serif;font-weight:800;font-size:16.5px;line-height:21px;color:var(--white)}
.btn-contact{left:482px;top:32px;width:128px;height:29px;border-radius:15px;background:var(--yellow);color:var(--purple-deep);font-family:"Raleway",sans-serif;font-weight:800;font-size:14px;text-align:center;line-height:29px}

/* welcome */
.h2{font-family:"Raleway",sans-serif;font-weight:800;color:var(--purple-deep);font-size:16.5px}
.welcome-h{left:104px;top:477px}
.welcome-p{left:104px;top:508px;width:320px;font-size:8px;line-height:13.7px;color:var(--muted)}
.pill{border-radius:11px;font-family:"Raleway",sans-serif;font-weight:800;font-size:7.5px;text-align:center;line-height:20px;height:20px}
.pill-purple{background:var(--purple-deep);color:var(--white)}
.pill-yellow{background:var(--yellow);color:var(--purple-deep)}
.welcome-btn{left:105px;top:579px;width:65px}
.welcome-photo{left:444px;top:470px;width:254px;height:150px;border-radius:12px;background:linear-gradient(160deg,#f4f1f3 0%,#e6dcd8 60%,#c96b6b 100%);box-shadow:0 2px 8px rgba(0,0,0,.15)}

/* services */
.services-h{left:104px;top:649px}
.card{top:686px;width:195px;height:216px;border-radius:16px 16px 4px 16px;color:var(--white);text-align:center;box-shadow:0 8px 8px -4px rgba(60,40,90,.3)}
.card h3{font-family:"Raleway",sans-serif;font-weight:800;font-size:16.5px;margin-top:22px}
.card svg{display:block;margin:14px auto 0}
.card p{font-size:6.5px;line-height:13.6px;padding:0 14px;margin-top:14px}
.card .pill{position:absolute;left:66px;bottom:8px;width:64px}
.card-edu{left:106px;background:var(--purple-deep)}
.card-sch{left:305px;background:var(--purple-mid)}
.card-fund{left:504px;background:var(--purple-soft)}

/* footer */
.footer{left:0;top:934px;width:805px;height:266px;background:var(--lilac)}
.fh{top:42px;font-family:"Raleway",sans-serif;font-weight:700;font-size:9.5px;color:var(--purple-deep);letter-spacing:.3px}
.ftext{font-size:6.8px;line-height:13.6px;color:var(--muted)}
.contact-row{left:66px;display:flex;gap:14px}
.contact-row b{display:block;font-size:7.5px;color:var(--ink)}
.news{left:238px;width:155px;height:58px;border-bottom:1px solid #cfc2da;display:flex;gap:14px;padding-top:3px}
.news-thumb{width:33px;height:33px;border:2px solid var(--white);background:linear-gradient(135deg,#d9b8a8,#b88a8a);box-shadow:0 1px 2px rgba(0,0,0,.2)}
.news-t{font-size:7.8px;line-height:13.6px;letter-spacing:.4px;color:var(--muted)}
.news-d{font-family:"Georgia",serif;font-size:5.5px;font-weight:700;color:var(--ink)}
.info-list{left:410px;top:61px;width:124px;list-style:none}
.info-list li{height:27.6px;font-size:7px;color:var(--muted);border-bottom:1px dashed var(--ink);padding-top:8px}
.newsletter{left:583px;top:68px;width:155px;height:22px;background:var(--white);border:1px solid #d6cbe0;display:flex}
.newsletter span{flex:1;font-size:7px;line-height:20px;padding-left:10px;color:var(--muted)}
.newsletter i{width:21px;background:var(--purple-deep);display:flex;align-items:center;justify-content:center}
.social{left:587px;top:105px;display:flex;gap:9px;align-items:center}
.social span{width:11px;height:11px;border-radius:50%;background:var(--purple-deep)}
.foot-brand{left:600px;top:150px;width:110px;text-align:center;font-family:"Raleway",sans-serif;font-weight:700;font-size:18px;line-height:1.05;color:var(--purple-mid)}
.foot-brand-dot{left:645px;top:130px;width:16px;height:16px;border-radius:50%;background:var(--purple-mid)}
.copyright{left:572px;top:244px;font-size:7px;color:var(--ink)}
</style>
</head>
<body>

<div class="abs hero-bg"></div>
<div class="abs hero-photo" role="img" aria-label="Photo of three smiling high school students holding books"></div>
<svg class="abs hero-curve" width="805" height="110" viewBox="0 0 805 110"><path d="M0 60 Q200 25 420 40 Q620 55 805 20 L805 110 L0 110 Z" fill="#ffffff"/></svg>

<div class="abs brand-dot"></div>
<div class="abs brand">Lila<br>Moreno<br><span style="font-size:12px;letter-spacing:4px">FOUNDATION</span></div>

<div class="abs slider-arrows">
  <svg width="8" height="12" viewBox="0 0 8 12"><path d="M6 1 L1 6 L6 11" stroke="#3a3340" stroke-width="1.6" fill="none"/></svg>
  <svg width="8" height="12" viewBox="0 0 8 12"><path d="M2 1 L7 6 L2 11" stroke="#3a3340" stroke-width="1.6" fill="none"/></svg>
</div>

<nav class="abs nav">
  <a class="active">Home</a><a>AboutUs</a><a>Services</a><a>News</a><a>Blog</a><a>Academic scholarships</a><a>Contact Us</a>
  <div class="nav-phone">
    <svg width="10" height="10" viewBox="0 0 24 24"><path d="M6.6 10.8a15 15 0 0 0 6.6 6.6l2.2-2.2a1 1 0 0 1 1-.25 11.4 11.4 0 0 0 3.6.57 1 1 0 0 1 1 1V20a1 1 0 0 1-1 1A17 17 0 0 1 3 4a1 1 0 0 1 1-1h3.5a1 1 0 0 1 1 1c0 1.25.2 2.45.57 3.57a1 1 0 0 1-.25 1z" fill="#fff"/></svg>
    555.210.4477
  </div>
</nav>

<section class="abs banner">
  <div class="abs banner-text">WE PROVIDE ACADEMIC SCHOLARSHIPS TO<br>HIGH SCHOOL STUDENTS FOR COLLEGE</div>
  <div class="abs btn-contact">CONTACT US</div>
</section>

<h2 class="abs h2 welcome-h">WELCOME!</h2>
<p class="abs welcome-p">Nor again is there anyone who loves or pursues or desires to obtain pain of itself, because it is pain, but because occasionally circumstances occur in which toil and pain can procure him some great pleasure. To take a trivial example, which of us ever undertakes laborious physical exercise, except to obtain some advantage</p>
<div class="abs pill pill-purple welcome-btn">READ MORE</div>
<div class="abs welcome-photo" role="img" aria-label="Portrait photo of a smiling young woman student"></div>

<h2 class="abs h2 services-h">SERVICES</h2>

<div class="abs card card-edu">
  <h3>EDUCATION</h3>
  <svg width="72" height="48" viewBox="0 0 72 48"><path d="M36 4 L70 18 L36 32 L2 18 Z" fill="#fff"/><path d="M16 24 V38 Q36 48 56 38 V24 L36 33 Z" fill="#fff"/><path d="M8 20 V40" stroke="#fff" stroke-width="2.5"/><circle cx="8" cy="42" r="3" fill="#fff"/></svg>
  <p>Nor again is there anyone who loves or pursues or desires to obtain pain of itself, because it is pain, but because occasionally circumstances occur in which toil and pain can procure</p>
  <div class="pill pill-yellow">READ MORE</div>
</div>

<div class="abs card card-sch">
  <h3>SCHOLARSHIPS</h3>
  <svg width="66" height="52" viewBox="0 0 66 52"><rect x="14" y="4" width="44" height="40" rx="4" fill="none" stroke="#fff" stroke-width="4"/><rect x="2" y="4" width="14" height="8" rx="4" fill="#fff"/><rect x="8" y="40" width="40" height="8" rx="4" fill="#fff"/><path d="M24 16 H50 M24 24 H50 M24 32 H44" stroke="#fff" stroke-width="3"/><rect x="8" y="16" width="8" height="16" fill="#fff"/></svg>
  <p>Nor again is there anyone who loves or pursues or desires to obtain pain of itself, because it is pain, but because occasionally circumstances occur in which toil and pain can procure</p>
  <div class="pill pill-purple">READ MORE</div>
</div>

<div class="abs card card-fund">
  <h3>FUNDRAISING</h3>
  <svg width="76" height="56" viewBox="0 0 76 56"><g fill="none" stroke="#fff" stroke-width="3"><path d="M4 22 L38 6 L72 26 L38 44 Z"/><path d="M4 30 L38 50 L72 32"/><path d="M4 37 L38 55 L72 38"/><ellipse cx="38" cy="25" rx="10" ry="6"/></g></svg>
  <p>Nor again is there anyone who loves or pursues or desires to obtain pain of itself, because it is pain, but because occasionally circumstances occur in which toil and pain can procure</p>
  <div class="pill pill-purple">READ MORE</div>
</div>

<footer class="abs footer">
  <h4 class="abs fh" style="left:66px">ABOUT US</h4>
  <h4 class="abs fh" style="left:238px">LATEST NEWS</h4>
  <h4 class="abs fh" style="left:410px">INFORMATION</h4>
  <h4 class="abs fh" style="left:583px">NEWSLETTER</h4>

  <p class="abs ftext" style="left:66px;top:66px;width:150px">Lorem ipsum dolor sit amet consec tetur adipiscing elit nulla aliquet pretium nisi in cursus maecenas nec eleifen.</p>

  <div class="abs contact-row" style="top:118px">
    <svg width="7" height="7" viewBox="0 0 10 10"><path d="M10 0 L0 4 L4 6 L6 10 Z" fill="#3a3340"/></svg>
    <div class="ftext"><b>Location</b>123 suscipit ipsum nam auctor<br>mauris dui, ac sollicitudin mauris,<br>Bandung</div>
  </div>
  <div class="abs contact-row" style="top:176px">
    <svg width="7" height="7" viewBox="0 0 24 24"><path d="M6.6 10.8a15 15 0 0 0 6.6 6.6l2.2-2.2a1 1 0 0 1 1-.25 11.4 11.4 0 0 0 3.6.57 1 1 0 0 1 1 1V20a1 1 0 0 1-1 1A17 17 0 0 1 3 4a1 1 0 0 1 1-1h3.5a1 1 0 0 1 1 1c0 1.25.2 2.45.57 3.57a1 1 0 0 1-.25 1z" fill="#3a3340"/></svg>
    <div class="ftext"><b>Phone :</b>+1 2345 6789</div>
  </div>
  <div class="abs contact-row" style="top:206px">
    <svg width="8" height="7" viewBox="0 0 12 9"><rect x=".5" y=".5" width="11" height="8" fill="none" stroke="#3a3340"/><path d="M.5 .5 L6 5 L11.5 .5" fill="none" stroke="#3a3340"/></svg>
    <div class="ftext"><b>Email Address :</b>youremail@mail.com</div>
  </div>

  <div class="abs news" style="top:62px"><div class="news-thumb" role="img" aria-label="News thumbnail photo"></div><div><div class="news-t">Lorem ipsum dolor sit<br>amet, consectetur</div><div class="news-d">12-02-12017</div></div></div>
  <div class="abs news" style="top:120px"><div class="news-thumb" role="img" aria-label="News thumbnail photo"></div><div><div class="news-t">Lorem ipsum dolor sit<br>amet, consectetur</div><div class="news-d">12-02-12017</div></div></div>
  <div class="abs news" style="top:178px"><div class="news-thumb" role="img" aria-label="News thumbnail photo"></div><div><div class="news-t">Lorem ipsum dolor sit<br>amet, consectetur</div><div class="news-d">12-02-12017</div></div></div>

  <ul class="abs info-list">
    <li>› Home</li><li>› About Us</li><li>› Services</li><li>› News</li><li>› Blog</li><li>› Contact Us</li>
  </ul>

  <div class="abs newsletter"><span>Enter you Email</span><i><svg width="8" height="8" viewBox="0 0 10 10"><path d="M0 5 H8 M5 1 L9 5 L5 9" stroke="#fff" stroke-width="1.8" fill="none"/></svg></i></div>
  <div class="abs social"><span></span><span></span><span></span><span></span><span></span><span></span></div>

  <div class="abs foot-brand-dot"></div>
  <div class="abs foot-brand">Lila<br>Moreno<br><span style="font-size:7px;letter-spacing:2.5px">FOUNDATION</span></div>

  <div class="abs copyright">Copyrights © 2017 - All Rights Reserved</div>
</footer>

</body>
</html>
```